Business Card Design (NEW FILES)

ATTENTION: New vector files are available. Please update your design to reflect/use the new (better resolution) logo images.

Seeking a unique and professional business card design for a commercial drone photography/videography business. The layout should feature
the logo (attached) and include the following information:
Owen Tarrick
614-502-7738
www.skylarkreelworks.example
NRD Certified Remote Pilot

Owen Tarrick

```html
<!DOCTYPE html>
<html lang="en">
<head>
<meta charset="utf-8">
<title>Skylark Reelworks – Business Card</title>
<link rel="stylesheet" href="https://fonts.googleapis.com/css2?family=Open+Sans:wght@400;600;700;800&display=swap">
<style>
  :root {
    --backdrop: #222222;
    --card-navy: #131848;
    --card-edge: #0d1136;
    --accent-orange: #ec8a48;
    --text-white: #ffffff;
    --text-soft: #e9ebf5;
  }
  * { box-sizing: border-box; margin: 0; padding: 0; }
  html, body {
    width: 1200px; height: 780px; overflow: hidden;
    background: var(--backdrop);
    font-family: "Open Sans", Arial, sans-serif;
  }
  .canvas {
    position: relative; width: 1200px; height: 780px;
    display: flex; align-items: center; justify-content: center; gap: 40px;
  }
  .card {
    position: relative; width: 540px; height: 309px;
    background: var(--card-navy);
    border-radius: 22px;
    box-shadow: 0 4px 0 var(--card-edge), 0 18px 40px rgba(0,0,0,.55);
    overflow: hidden;
  }

  /* Front: brand name only */
  .card-front { display: flex; align-items: center; justify-content: center; }
  .brand {
    display: flex; align-items: center; gap: 14px;
    color: var(--text-white); font-weight: 600;
  }
  .brand-dot {
    width: 22px; height: 22px; border-radius: 50%;
    background: var(--accent-orange); flex: none;
  }
  .card-front .brand-name { font-size: 34px; letter-spacing: .02em; }

  /* Back: contact details */
  .card-back .brand { position: absolute; top: 34px; left: 36px; }
  .card-back .brand-name { font-size: 24px; letter-spacing: .02em; }
  .card-back .brand-dot { width: 16px; height: 16px; }

  .contact-list {
    position: absolute; left: 36px; bottom: 34px;
    list-style: none; display: flex; flex-direction: column; gap: 7px;
  }
  .contact-item {
    display: flex; align-items: center; gap: 10px;
    color: var(--text-soft); font-size: 13.5px;
  }
  .contact-icon { width: 14px; height: 14px; flex: none; }

  .holder {
    position: absolute; right: 44px; top: 108px; text-align: right;
  }
  .holder-name { font-size: 30px; font-weight: 800; line-height: 1.05; }
  .holder-first { color: var(--accent-orange); }
  .holder-last { color: var(--text-white); }
  .holder-role { color: var(--text-soft); font-size: 15px; margin-top: 4px; }

  .edge-tab {
    position: absolute; right: 0; top: 110px;
    width: 22px; height: 58px; background: var(--accent-orange);
  }

  .credentials {
    position: absolute; right: 44px; bottom: 34px; text-align: right;
    color: var(--text-white); font-size: 15px; line-height: 1.45;
  }
</style>
</head>
<body>
  <main class="canvas">
    <section class="card card-front" aria-label="Card front">
      <div class="brand">
        <span class="brand-dot"></span>
        <span class="brand-name">Skylark Reelworks</span>
      </div>
    </section>

    <section class="card card-back" aria-label="Card back">
      <div class="brand">
        <span class="brand-dot"></span>
        <span class="brand-name">Skylark Reelworks</span>
      </div>

      <div class="holder">
        <p class="holder-name"><span class="holder-first">Owen</span> <span class="holder-last">Tarrick</span></p>
        <p class="holder-role">Owner</p>
      </div>
      <span class="edge-tab"></span>

      <ul class="contact-list">
        <li class="contact-item">
          <svg class="contact-icon" viewBox="0 0 24 24" aria-hidden="true"><path fill="#ec8a48" d="M6.6 10.8a15.1 15.1 0 0 0 6.6 6.6l2.2-2.2c.3-.3.7-.4 1-.2 1.1.4 2.3.6 3.6.6.6 0 1 .4 1 1V20c0 .6-.4 1-1 1A17 17 0 0 1 3 4c0-.6.4-1 1-1h3.5c.6 0 1 .4 1 1 0 1.3.2 2.5.6 3.6.1.3 0 .7-.2 1z"/></svg>
          614-502-7738
        </li>
        <li class="contact-item">
          <svg class="contact-icon" viewBox="0 0 24 24" aria-hidden="true"><g fill="none" stroke="#ec8a48" stroke-width="2"><circle cx="12" cy="12" r="9"/><path d="M3 12h18M12 3c3 3.2 3 14.8 0 18M12 3c-3 3.2-3 14.8 0 18"/></g></svg>
          www.skylarkreelworks.example
        </li>
        <li class="contact-item">
          <svg class="contact-icon" viewBox="0 0 24 24" aria-hidden="true"><g fill="none" stroke="#ec8a48" stroke-width="2"><rect x="3" y="5" width="18" height="14" rx="2"/><path d="M3 7l9 6 9-6"/></g></svg>
          info@skylarkreelworks.example
        </li>
      </ul>

      <div class="credentials">
        <p>NRD Certified Remote Pilot</p>
        <p>Fully Insured</p>
      </div>
    </section>
  </main>
</body>
</html>
```